Webdesign Hauskranken- und Tagespflege „Am Lindenhof“
Zielgruppe
Die Hauskranken- und Tagespflege „Am Lindenhof“ in Chemnitz ist ein unabhängiges, privat geführtes Unternehmen im Bereich der ambulanten und teilstationären Kranken- und Seniorenpflege. Seit der Gründung am 1. Mai 2007 stehen wir für eine zuverlässige, individuelle und herzliche Betreuung unserer Klientinnen und Klienten.
Das Team ist ein engagiertes Pflegeteam und auf über 35 qualifizierte Mitarbeiterinnen und Mitarbeiter angewachsen. Gemeinsam setzen wir uns täglich dafür ein, Menschen mit Pflegebedarf eine bestmögliche Versorgung und ein hohes Maß an Lebensqualität zu ermöglichen.
Unsere Firmenphilosophie basiert auf Wertschätzung, Vertrauen und Respekt – sowohl im Umgang mit unseren Klientinnen und Klienten sowie deren Angehörigen als auch innerhalb unseres Teams. Eine persönliche, einfühlsame und fachlich kompetente Betreuung steht für uns an erster Stelle.
Ob Grundpflege oder Behandlungspflege – bei uns sind Sie in guten Händen. Wir begleiten unsere Klientinnen und Klienten mit Fürsorge, Fachkompetenz und Herz und unterstützen sie dabei, ihren Alltag so selbstbestimmt wie möglich zu gestalten.
Gleichzeitig entlasten wir Angehörige, Freunde und Bekannte, indem wir ihnen Sicherheit geben und Freiräume schaffen. So bleibt mehr Zeit für gemeinsame, unbeschwerte Momente mit den Menschen, die ihnen am Herzen liegen.
Unsere Tagespflege bietet Platz für 18 Gäste. Der große Aufenthaltsraum mit offener Küche lädt zum gemütlichen Beisammensein ein. In unserem Ruheraum können sich unsere Gäste bei Bedarf zurückziehen und sich ausruhen, auch Therapien (Logopädie, Ergotherapie, Physiotherapie…) werden darin durchgeführt. Der Aufenthaltsraum ist zum Teil eingerichtet wie eine gemütliche Wohnstube, ihre Einrichtung erinnert an frühere Zeiten. Gemütliche Ruhesessel laden zum Entspannen ein.
Der persönliche Kontakt und das Vertrauen unserer Patientinnen und Patienten bilden dabei st..
Aufgabenstellung
Ziele des Relaunchs:
modernes, freundliches und barrierearmes Design
klare Benutzerführung für Senioren und Angehörige
Hinweis zum Rückrufservice
Notfallnummer dauerhaft sichtbar
schnelle Kontaktaufnahme (Telefon, Rückruf, Kontaktformular)
bessere Auffindbarkeit bei Google (SEO)
Vertrauen durch authentische Bilder, Teamvorstellung und Bewertungen

```html
<!DOCTYPE html>
<html lang="de">
<head>
<meta charset="utf-8">
<title>Hauskranken- und Tagespflege „Am Lindenhof“ – Chemnitz</title>
<link href="https://fonts.googleapis.com/css2?family=Nunito:ital,wght@0,400;0,600;0,700;0,800;1,400&display=swap" rel="stylesheet">
<style>
:root{
  --bg:#000;
  --card:#0b0b0b;
  --text:#fff;
  --muted:#d6d6d6;
  --accent:#ffe600;
  --line:#3a3a3a;
  --field:#000;
}
*{box-sizing:border-box;margin:0;padding:0}
html,body{width:1200px;height:4676px;overflow:hidden}
body{background:var(--bg);color:var(--text);font-family:"Nunito",sans-serif;position:relative}
.abs{position:absolute}
svg.ic{fill:none;stroke:currentColor;stroke-width:2;stroke-linecap:round;stroke-linejoin:round}
.y{color:var(--accent)}
.center{left:0;width:1200px;text-align:center}
/* top bar */
.topbar{top:0;left:0;width:1200px;height:25px;font-size:12px;font-weight:600;display:flex;justify-content:space-between;align-items:center;padding:0 20px}
.topbar span{display:flex;align-items:center;gap:5px}
/* header */
.header{top:25px;left:0;width:1200px;height:66px;display:flex;align-items:center;padding:0 20px}
.brand{display:flex;align-items:center;gap:10px}
.brand .dot{width:30px;height:30px;border-radius:50%;background:var(--accent)}
.brand b{display:block;font-size:13px;color:var(--accent);font-weight:800}
.brand small{display:block;font-size:9px;color:var(--accent);font-weight:600}
.nav{display:flex;gap:28px;margin-left:130px;font-size:16px;font-weight:600;color:var(--accent)}
.header .call{margin-left:auto;color:var(--accent);font-weight:800;font-size:17px;display:flex;gap:8px;align-items:center}
/* hero */
.hero{top:91px;left:0;width:1200px;height:532px;background:linear-gradient(100deg,#6b5d4a 0%,#a89a80 35%,#8fa6a8 60%,#cfc6b4 100%)}
.badge{left:20px;top:76px;background:#000;border-radius:14px;font-size:11px;font-weight:700;padding:5px 12px}
.hero h1{left:20px;top:120px;font-size:44px;line-height:54px;font-weight:800}
.hero h1 span,.hero .sub span{background:#000;padding:0 4px 0 0;box-decoration-break:clone;-webkit-box-decoration-break:clone}
.hero .sub{left:20px;top:302px;font-size:21px;line-height:28px}
.hero .sub span+br+span{font-weight:700}
.btn{top:384px;height:73px;border-radius:12px;display:flex;align-items:center;gap:14px;padding:0 22px;font-weight:800;font-size:17px;line-height:22px;color:var(--accent)}
.btn.solid{left:20px;width:303px;background:#000}
.btn.ghost{left:338px;width:243px;background:rgba(0,0,0,.25);border:2px solid var(--accent)}
.access{right:8px;top:38px;width:18px;height:18px;border-radius:50%;background:#111}
/* quick bar */
.quick{top:623px;left:0;width:1200px;height:94px;display:flex;padding:0 44px}
.quick div{flex:1;display:flex;align-items:center;gap:22px;color:var(--accent)}
.quick b{display:block;font-size:16px;font-weight:800}
.quick small{display:block;font-size:12px}
/* headings */
h2{font-size:30px;font-weight:800}
.lead{font-size:16px;color:var(--muted);line-height:24px}
/* service cards */
.card{top:918px;width:566px;height:416px;background:var(--card);border-radius:10px;overflow:hidden}
.card .img{height:213px;position:relative}
.card .img i{position:absolute;left:20px;top:20px;width:40px;height:40px;border-radius:50%;background:#000;display:flex;align-items:center;justify-content:center;color:#fff}
.card .body{padding:26px 27px}
.card h3{font-size:20px;font-weight:700;margin-bottom:14px}
.card p{font-size:15px;line-height:23px;color:var(--muted)}
.more{color:var(--accent);font-weight:800;font-size:15px;display:inline-flex;gap:8px;align-items:center;margin-top:22px}
/* values */
.vals{top:1580px;left:20px;width:1160px;display:flex}
.vals div{flex:1;text-align:center}
.vals svg{margin-bottom:20px}
.vals b{display:block;font-size:16px;font-weight:700;margin-bottom:8px}
.vals p{font-size:15px;line-height:23px;color:var(--muted);padding:0 40px}
.rating{top:1794px;font-size:15px;font-weight:700;display:flex;justify-content:center;align-items:center;gap:10px}
.stars{display:flex;gap:2px;color:#f0a622}
.quote{top:1890px;width:500px}
.quote .mark{font-size:58px;font-weight:800;color:#6f5a12;line-height:30px;font-family:Georgia,serif}
.quote p{font-size:15px;line-height:23px;font-style:italic;color:var(--muted);margin-top:8px}
.quote .who{font-size:15px;margin-top:14px;font-style:normal}
/* team */
.teamimg{top:2274px;left:20px;width:1160px;height:350px;border-radius:10px;background:linear-gradient(90deg,#3c3c3c,#c9c9c9 30%,#e5e5e5 55%,#9a9a9a 80%,#2a2a2a)}
/* daycare */
.day h2{left:20px;top:2905px}
.day p{left:20px;top:3030px;width:560px;font-size:16px;line-height:27.5px;color:var(--muted)}
.ticks{left:20px;top:3190px;list-style:none;font-size:15px;color:var(--muted)}
.ticks li{display:flex;align-items:center;gap:14px;height:37px}
.ph1{left:621px;top:2982px;width:319px;height:212px;border-radius:8px;background:linear-gradient(135deg,#1a3f8a,#6c7fa8 50%,#c9c2b8)}
.ph2{left:621px;top:3209px;width:272px;height:158px;border-radius:8px;background:linear-gradient(135deg,#c97f63,#6e7a8c 50%,#3c4e66)}
/* contact */
.form{left:47px;top:3662px;width:507px}
.form h3,.kontakt h3{font-size:20px;font-weight:700}
.form .hint{font-size:14px;color:var(--muted);margin-top:6px}
label{display:block;font-size:15px;font-weight:700;margin-bottom:6px}
.field{border:1px solid #cfcfcf;border-radius:8px;background:var(--field);height:46px}
.row{display:flex;gap:19px}
.row>div{flex:1}
.grp{margin-top:20px}
.select{display:flex;align-items:center;justify-content:space-between;padding:0 16px;font-size:15px}
.submit{display:flex;justify-content:center;gap:10px;align-items:center;font-weight:800;font-size:16px;margin-top:30px}
.kontakt{left:646px;top:3662px;width:534px}
.kitem{display:flex;gap:22px;margin-top:26px;align-items:flex-start}
.kitem svg{margin-top:8px;color:var(--accent)}
.kitem small{display:block;font-size:10px;font-weight:700;text-transform:uppercase;color:var(--muted)}
.kitem b{display:block;font-size:17px;font-weight:800;line-height:23px}
.map{left:621px;top:3944px;width:559px;height:240px;border-radius:8px;background:linear-gradient(135deg,#dfe7d2,#eef0ea 50%,#d9e2cf)}
/* footer */
.footer{top:4374px;left:20px;width:1160px}
.fcol{position:absolute;top:0}
.fcol h4{font-size:14px;font-weight:700;margin-bottom:14px}
.fcol a{display:block;font-size:15px;color:var(--accent);text-decoration:none;line-height:30px}
.divider{top:4588px;left:20px;width:1160px;height:1px;background:var(--line)}
.copy{top:4612px;font-size:12px;color:var(--muted)}
</style>
</head>
<body>

<div class="abs topbar">
  <span><svg class="ic" width="12" height="12" viewBox="0 0 24 24"><circle cx="12" cy="12" r="10"/><path d="M12 6v6l4 2"/></svg>Mo-Do 9:00-15:00 Uhr · Fr 9:00-14:00 Uhr</span>
  <span class="y"><svg class="ic" width="12" height="12" viewBox="0 0 24 24"><path d="M22 16.9v3a2 2 0 0 1-2.2 2 19.8 19.8 0 0 1-8.6-3.1 19.5 19.5 0 0 1-6-6A19.8 19.8 0 0 1 2.1 4.2 2 2 0 0 1 4.1 2h3a2 2 0 0 1 2 1.7c.1.9.4 1.8.7 2.7a2 2 0 0 1-.5 2.1L8 9.8a16 16 0 0 0 6 6l1.3-1.3a2 2 0 0 1 2.1-.4c.9.3 1.8.6 2.7.7a2 2 0 0 1 1.7 2z"/></svg>24h-Hotline: 0371 / 4690218</span>
</div>

<header class="abs header">
  <div class="brand"><div class="dot"></div><div><b>Am Lindenhof</b><small>Hauskranken- &amp; Tagespflege</small></div></div>
  <nav class="nav"><span>Über uns</span><span>Hauskrankenpflege</span><span>Tagespflege</span><span>Unser Team</span><span>Kontakt</span></nav>
  <div class="call"><svg class="ic" width="16" height="16" viewBox="0 0 24 24"><path d="M22 16.9v3a2 2 0 0 1-2.2 2 19.8 19.8 0 0 1-8.6-3.1 19.5 19.5 0 0 1-6-6A19.8 19.8 0 0 1 2.1 4.2 2 2 0 0 1 4.1 2h3a2 2 0 0 1 2 1.7c.1.9.4 1.8.7 2.7a2 2 0 0 1-.5 2.1L8 9.8a16 16 0 0 0 6 6l1.3-1.3a2 2 0 0 1 2.1-.4c.9.3 1.8.6 2.7.7a2 2 0 0 1 1.7 2z"/></svg>Jetzt anrufen</div>
</header>

<section class="abs hero" role="img" aria-label="Foto: Pflegekraft beugt sich zu einer älteren Dame im Rollstuhl, im Hintergrund ein Senior">
  <div class="abs badge">Vertrauenspflege seit 2007</div>
  <h1 class="abs"><span>Ihr Pflegeteam aus<br>Chemnitz –<br>mit Herz &amp; Fachkompetenz</span></h1>
  <p class="abs sub"><span>Ambulante Hauskrankenpflege &amp; Tagespflege seit 2007</span><br><span>35+ Mitarbeiterinnen &amp; Mitarbeiter</span></p>
  <div class="abs btn solid"><svg class="ic" width="18" height="18" viewBox="0 0 24 24"><path d="M22 16.9v3a2 2 0 0 1-2.2 2 19.8 19.8 0 0 1-8.6-3.1 19.5 19.5 0 0 1-6-6A19.8 19.8 0 0 1 2.1 4.2 2 2 0 0 1 4.1 2h3a2 2 0 0 1 2 1.7c.1.9.4 1.8.7 2.7a2 2 0 0 1-.5 2.1L8 9.8a16 16 0 0 0 6 6l1.3-1.3a2 2 0 0 1 2.1-.4c.9.3 1.8.6 2.7.7a2 2 0 0 1 1.7 2z"/></svg><span>Jetzt anrufen: 0371 /<br>4690218</span></div>
  <div class="abs btn ghost"><svg class="ic" width="18" height="18" viewBox="0 0 24 24"><path d="M22 16.9v3a2 2 0 0 1-2.2 2 19.8 19.8 0 0 1-8.6-3.1 19.5 19.5 0 0 1-6-6A19.8 19.8 0 0 1 2.1 4.2 2 2 0 0 1 4.1 2h3a2 2 0 0 1 2 1.7c.1.9.4 1.8.7 2.7a2 2 0 0 1-.5 2.1L8 9.8a16 16 0 0 0 6 6l1.3-1.3a2 2 0 0 1 2.1-.4c.9.3 1.8.6 2.7.7a2 2 0 0 1 1.7 2z"/><path d="M15 2v5h5"/></svg><span>Rückruf<br>vereinbaren</span></div>
  <div class="abs access"></div>
</section>

<div class="abs quick">
  <div><svg class="ic" width="22" height="22" viewBox="0 0 24 24"><path d="M22 16.9v3a2 2 0 0 1-2.2 2 19.8 19.8 0 0 1-8.6-3.1 19.5 19.5 0 0 1-6-6A19.8 19.8 0 0 1 2.1 4.2 2 2 0 0 1 4.1 2h3a2 2 0 0 1 2 1.7c.1.9.4 1.8.7 2.7a2 2 0 0 1-.5 2.1L8 9.8a16 16 0 0 0 6 6l1.3-1.3a2 2 0 0 1 2.1-.4c.9.3 1.8.6 2.7.7a2 2 0 0 1 1.7 2z"/></svg><span><b>Anrufen</b><small>24h-Hotline · 0371 / 4690218</small></span></div>
  <div><svg class="ic" width="22" height="22" viewBox="0 0 24 24"><path d="M22 16.9v3a2 2 0 0 1-2.2 2 19.8 19.8 0 0 1-8.6-3.1 19.5 19.5 0 0 1-6-6A19.8 19.8 0 0 1 2.1 4.2 2 2 0 0 1 4.1 2h3a2 2 0 0 1 2 1.7c.1.9.4 1.8.7 2.7a2 2 0 0 1-.5 2.1L8 9.8a16 16 0 0 0 6 6l1.3-1.3a2 2 0 0 1 2.1-.4c.9.3 1.8.6 2.7.7a2 2 0 0 1 1.7 2z"/><path d="M15 2v5h5"/></svg><span><b>Rückruf anfordern</b><small>Wir rufen Sie gerne zurück</small></span></div>
  <div><svg class="ic" width="22" height="22" viewBox="0 0 24 24"><rect x="2" y="4" width="20" height="16" rx="2"/><path d="m22 7-10 6L2 7"/></svg><span><b>Nachricht senden</b><small>Schreiben Sie uns direkt</small></span></div>
</div>

<h2 class="abs center" style="top:780px">Unsere Pflegeleistungen für Sie</h2>
<p class="abs lead" style="top:832px;left:320px;width:560px;text-align:center">Von der ambulanten Pflege zu Hause bis zur Tagespflege – wir sind für Sie da.</p>

<article class="abs card" style="left:20px">
  <div class="img" role="img" aria-label="Foto: Pflegerin hält die Hände einer lachenden Seniorin" style="background:linear-gradient(120deg,#7a1f1f,#b7a489 50%,#e6e0d4)"><i><svg class="ic" width="18" height="18" viewBox="0 0 24 24"><path d="M3 10 12 3l9 7v10a1 1 0 0 1-1 1h-5v-6H9v6H4a1 1 0 0 1-1-1z"/></svg></i></div>
  <div class="body"><h3>Hauskrankenpflege</h3><p>Grundpflege &amp; Behandlungspflege direkt bei Ihnen zu Hause – individuell, zuverlässig und mit Einfühlungsvermögen.</p><span class="more">Mehr erfahren <svg class="ic" width="14" height="14" viewBox="0 0 24 24"><path d="M5 12h14M13 6l6 6-6 6"/></svg></span></div>
</article>
<article class="abs card" style="left:614px">
  <div class="img" role="img" aria-label="Foto: Seniorinnen und Senioren spielen gemeinsam am Tisch" style="background:linear-gradient(120deg,#3e5a8a,#c7b6a6 50%,#d7a43a 80%,#2d6a6a)"><i><svg class="ic" width="18" height="18" viewBox="0 0 24 24"><circle cx="12" cy="12" r="4"/><path d="M12 2v2M12 20v2M4.9 4.9l1.4 1.4M17.7 17.7l1.4 1.4M2 12h2M20 12h2M4.9 19.1l1.4-1.4M17.7 6.3l1.4-1.4"/></svg></i></div>
  <div class="body"><h3>Tagespflege</h3><p>18 Gästeplätze | Gemütliche Aufenthaltsräume | Therapien vor Ort (Logopädie, Ergo-, Physiotherapie) | Sicherheit &amp; soziale Teilhabe für Ihre Angehörigen.</p><span class="more">Tagespflege entdecken <svg class="ic" width="14" height="14" viewBox="0 0 24 24"><path d="M5 12h14M13 6l6 6-6 6"/></svg></span></div>
</article>

<h2 class="abs center" style="top:1467px">Pflege, auf die Sie sich verlassen können</h2>
<div class="abs vals">
  <div><svg class="ic" width="26" height="26" viewBox="0 0 24 24"><circle cx="9" cy="8" r="4"/><path d="M2 21v-1a6 6 0 0 1 12 0v1M16 4a4 4 0 0 1 0 8M22 21v-1a6 6 0 0 0-4-5.6"/></svg><b>35+ Mitarbeiterinnen</b><p>Qualifiziertes &amp; einfühlsames Pflegeteam</p></div>
  <div><svg class="ic" width="26" height="26" viewBox="0 0 24 24"><path d="M20.8 4.6a5.5 5.5 0 0 0-7.8 0L12 5.7l-1-1.1a5.5 5.5 0 0 0-7.8 7.8L12 21l8.8-8.6a5.5 5.5 0 0 0 0-7.8z"/></svg><b>Seit 2007 für Chemnitz</b><p>Fast 20 Jahre Vertrauen &amp; Erfahrung</p></div>
  <div><svg class="ic" width="26" height="26" viewBox="0 0 24 24"><path d="m12 2 3.1 6.3 6.9 1-5 4.9 1.2 6.8L12 17.8 5.8 21l1.2-6.8-5-4.9 6.9-1z"/></svg><b>Individuelle Betreuung</b><p>Ganz auf Ihre persönlichen Bedürfnisse abgestimmt</p></div>
</div>
<div class="abs center rating">Online-Bewertungen
  <span class="stars"><svg width="100" height="18" viewBox="0 0 100 18"><g fill="currentColor"><path id="s" d="m9 1 2.3 5 5.4.6-4 3.7 1.1 5.4L9 13l-4.8 2.7 1.1-5.4-4-3.7 5.4-.6z"/><use href="#s" x="20"/><use href="#s" x="40"/><use href="#s" x="60"/><use href="#s" x="80"/></g></svg></span>
  <span style="font-weight:600;font-size:14px">5,0</span>
</div>
<div class="abs quote" style="left:47px"><div class="mark">”</div><p>„Seit meine Mutter die Tagespflege besucht, blüht sie wieder auf. Das Team ist warmherzig und unglaublich geduldig. Ich kann nur jedem Angehörigen empfehlen.“</p><p class="who"><b>Frau K.</b> · Angehörige</p></div>
<div class="abs quote" style="left:637px"><div class="mark">”</div><p>„Die Hauskrankenpflege kam immer pünktlich und hat meinem Vater geholfen, so lange wie möglich zu Hause zu bleiben. Dafür bin ich sehr dankbar.“</p><p class="who"><b>Herr M.</b> · Angehöriger</p></div>

<h2 class="abs center" style="top:2197px">Unser engagiertes Pflegeteam</h2>
<div class="abs teamimg" role="img" aria-label="Schwarz-Weiß-Foto: Reihe von Pflegekräften in weißen Kitteln"></div>
<p class="abs lead" style="top:2652px;left:280px;width:640px;text-align:center">Über 35 qualifizierte Mitarbeiterinnen und Mitarbeiter, die sich täglich für Ihre Lebensqualität einsetzen – mit Fachkompetenz, Fürsorge und Herz.</p>
<div class="abs center" style="top:2738px"><span class="more" style="margin:0">Unser Team kennenlernen <svg class="ic" width="14" height="14" viewBox="0 0 24 24"><path d="M5 12h14M13 6l6 6-6 6"/></svg></span></div>

<section class="day">
  <h2 class="abs">Unsere Tagespflege – Ihr zweites Zuhause</h2>
  <p class="abs">18 Gästeplätze in gemütlicher Atmosphäre. Unser großer Aufenthaltsraum mit offener Küche lädt zum Beisammensein ein – wie in einer Wohnstube von früher. Im Ruheraum können sich Gäste erholen; Therapien (Logopädie, Ergotherapie, Physiotherapie) finden direkt vor Ort statt.</p>
  <ul class="abs ticks">
    <li><svg class="ic" width="12" height="12" viewBox="0 0 24 24"><path d="m4 12 5 5L20 6"/></svg>18 Gästeplätze in gemütlicher Atmosphäre</li>
    <li><svg class="ic" width="12" height="12" viewBox="0 0 24 24"><path d="m4 12 5 5L20 6"/></svg>Großer Aufenthaltsraum mit offener Küche</li>
    <li><svg class="ic" width="12" height="12" viewBox="0 0 24 24"><path d="m4 12 5 5L20 6"/></svg>Ruheraum zur Erholung</li>
    <li><svg class="ic" width="12" height="12" viewBox="0 0 24 24"><path d="m4 12 5 5L20 6"/></svg>Therapien vor Ort: Logopädie, Ergo- &amp; Physiotherapie</li>
  </ul>
  <div class="abs ph1" role="img" aria-label="Foto: zwei Seniorinnen im Gespräch im Aufenthaltsraum"></div>
  <div class="abs ph2" role="img" aria-label="Foto: Gäste der Tagespflege spielen Schach"></div>
</section>

<h2 class="abs center" style="top:3498px">Sprechen Sie uns an – wir sind für Sie da</h2>
<p class="abs lead" style="top:3549px;left:320px;width:560px;text-align:center">Nutzen Sie unser Rückruf-Formular oder rufen Sie unsere 24h-Hotline an.</p>

<form class="abs form">
  <h3>Rückruf anfordern</h3>
  <p class="hint">Wir rufen Sie innerhalb von 24 Stunden zurück.</p>
  <div class="row grp" style="margin-top:24px"><div><label>Vorname *</label><div class="field"></div></div><div><label>Name *</label><div class="field"></div></div></div>
  <div class="grp"><label>Telefonnummer *</label><div class="field"></div></div>
  <div class="grp" style="margin-top:30px"><label>Gewünschter Rückrufzeitraum</label><div class="field select">Bitte wählen<svg class="ic" width="10" height="10" viewBox="0 0 24 24"><path d="m6 9 6 6 6-6"/></svg></div></div>
  <div class="grp"><label>Nachricht (optional)</label><div class="field" style="height:115px"></div></div>
  <div class="submit"><svg class="ic" width="16" height="16" viewBox="0 0 24 24"><path d="M22 2 11 13M22 2l-7 20-4-9-9-4z"/></svg>Rückruf anfordern</div>
</form>

<div class="abs kontakt">
  <h3>Kontaktdaten</h3>
  <div class="kitem"><svg class="ic" width="18" height="18" viewBox="0 0 24 24"><path d="M22 16.9v3a2 2 0 0 1-2.2 2 19.8 19.8 0 0 1-8.6-3.1 19.5 19.5 0 0 1-6-6A19.8 19.8 0 0 1 2.1 4.2 2 2 0 0 1 4.1 2h3a2 2 0 0 1 2 1.7c.1.9.4 1.8.7 2.7a2 2 0 0 1-.5 2.1L8 9.8a16 16 0 0 0 6 6l1.3-1.3a2 2 0 0 1 2.1-.4c.9.3 1.8.6 2.7.7a2 2 0 0 1 1.7 2z"/></svg><div><small class="y">24h-Hotline</small><b class="y" style="font-size:20px">0371 / 4690218</b></div></div>
  <div class="kitem"><svg class="ic" width="18" height="18" viewBox="0 0 24 24" style="color:#fff"><path d="M20 10c0 6-8 12-8 12s-8-6-8-12a8 8 0 0 1 16 0z"/><circle cx="12" cy="10" r="3"/></svg><div><small>Adresse</small><b>Lindenweg 27, 09130 Chemnitz</b></div></div>
  <div class="kitem"><svg class="ic" width="18" height="18" viewBox="0 0 24 24" style="color:#fff"><circle cx="12" cy="12" r="10"/><path d="M12 6v6l4 2"/></svg><div><small>Öffnungszeiten</small><b>Mo–Do: 9:00–15:00 Uhr<br>Fr: 9:00–14:00 Uhr</b></div></div>
</div>
<div class="abs map" role="img" aria-label="Karte: Lage der Pflegeeinrichtung im Norden von Chemnitz"></div>

<footer class="abs footer">
  <div class="brand"><div class="dot"></div><div><b>Am Lindenhof</b><small style="color:#fff">Hauskranken- &amp; Tagespflege</small></div></div>
  <p style="font-size:15px;margin-top:20px">Pflege mit Herz – seit 2007 für Sie da.</p>
  <p class="y" style="font-size:16px;font-weight:800;margin-top:14px">☏ 24h-Hotline: 0371 / 4690218</p>
  <p style="font-size:12px;margin-top:10px;color:var(--muted)">Lindenweg 27, 09130 Chemnitz</p>
  <div class="fcol" style="left:597px"><h4>Navigation</h4><a>Über uns</a><a>Hauskrankenpflege</a><a>Tagespflege</a><a>Unser Team</a><a>Kontakt</a></div>
  <div class="fcol" style="left:895px"><h4>Rechtliches</h4><a>Datenschutz</a><a>Impressum</a><a>Barrierefreiheitserklärung</a></div>
</footer>
<div class="abs divider"></div>
<p class="abs center copy">© 2026 Hauskranken- und Tagespflege Am Lindenhof. Alle Rechte vorbehalten.</p>

</body>
</html>
```